TA BRAMLEY BUSINESS CARD DESIGN PROJECT

We need to utilize our logo that was expertly created on PixelHarbor and now need to match this with a business card design.

```html
<!DOCTYPE html>
<html lang="en">
<head>
<meta charset="utf-8">
<title>TA Bramley Business Card</title>
<link href="https://fonts.googleapis.com/css2?family=Montserrat:wght@400;500;700;800&display=swap" rel="stylesheet">
<style>
  :root {
    --backdrop: #d6d6d6;
    --card: #f4f4f4;
    --brand-blue: #0b3a9e;
    --ink: #1a1a1a;
    --white: #ffffff;
  }
  * { margin: 0; padding: 0; box-sizing: border-box; }
  html, body {
    width: 1200px;
    height: 1051px;
    overflow: hidden;
    background: var(--backdrop);
    font-family: "Montserrat", sans-serif;
  }
  .sheet {
    position: relative;
    width: 1200px;
    height: 1051px;
    display: flex;
    align-items: center;
    justify-content: center;
    gap: 50px;
  }
  .card {
    position: relative;
    width: 525px;
    height: 300px;
    background: var(--card);
    box-shadow: 0 10px 30px rgba(0,0,0,0.18);
    overflow: hidden;
  }
  .card-back { border-bottom: 4px solid var(--brand-blue); }

  .identity {
    position: absolute;
    top: 82px;
    right: 292px;
    text-align: right;
  }
  .identity-name {
    color: var(--brand-blue);
    font-weight: 800;
    font-size: 19px;
    letter-spacing: 0.2px;
  }
  .identity-role {
    color: var(--ink);
    font-size: 13px;
    margin-top: 2px;
  }
  .divider {
    position: absolute;
    left: 248px;
    top: 84px;
    width: 2px;
    height: 88px;
    background: var(--brand-blue);
  }
  .contact-list {
    position: absolute;
    left: 262px;
    top: 92px;
    list-style: none;
  }
  .contact-item {
    display: flex;
    align-items: center;
    gap: 8px;
    color: var(--ink);
    font-size: 14px;
    line-height: 24px;
  }
  .contact-icon { width: 12px; height: 12px; fill: var(--brand-blue); flex: none; }

  .address-band {
    position: absolute;
    left: 0;
    right: 0;
    top: 204px;
    height: 30px;
    background: var(--brand-blue);
    color: var(--white);
    font-size: 13px;
    display: flex;
    align-items: center;
    justify-content: center;
  }

  .card-front {
    display: flex;
    align-items: center;
    justify-content: center;
    gap: 16px;
    border-bottom: 4px solid var(--brand-blue);
  }
  .brand-dot {
    width: 34px;
    height: 34px;
    border-radius: 50%;
    background: var(--brand-blue);
  }
  .brand-name {
    color: var(--brand-blue);
    font-weight: 800;
    font-size: 44px;
    letter-spacing: 4px;
  }
</style>
</head>
<body>
<main class="sheet">
  <section class="card card-back">
    <div class="identity">
      <p class="identity-name">JORDAN ELLIS</p>
      <p class="identity-role">Managing Director</p>
    </div>
    <div class="divider"></div>
    <ul class="contact-list">
      <li class="contact-item">
        <svg class="contact-icon" viewBox="0 0 24 24"><path d="M6.6 10.8a15.1 15.1 0 0 0 6.6 6.6l2.2-2.2a1 1 0 0 1 1-.25 11.4 11.4 0 0 0 3.6.57 1 1 0 0 1 1 1V20a1 1 0 0 1-1 1A17 17 0 0 1 3 4a1 1 0 0 1 1-1h3.5a1 1 0 0 1 1 1c0 1.25.2 2.45.57 3.57a1 1 0 0 1-.25 1z"/></svg>
        123 456 789
      </li>
      <li class="contact-item">
        <svg class="contact-icon" viewBox="0 0 24 24"><path d="M2 5h20v2l-10 6L2 7z M2 9l10 6 10-6v10H2z"/></svg>
        info@tabramley.com
      </li>
      <li class="contact-item">
        <svg class="contact-icon" viewBox="0 0 24 24"><circle cx="12" cy="12" r="10"/><path d="M2 12h20M12 2c3 3 3 17 0 20M12 2c-3 3-3 17 0 20" stroke="#f4f4f4" stroke-width="1.5" fill="none"/></svg>
        www.tabramley.com
      </li>
    </ul>
    <div class="address-band">Your address, City State, Zip 1234</div>
  </section>

  <section class="card card-front">
    <span class="brand-dot"></span>
    <span class="brand-name">TA BRAMLEY</span>
  </section>
</main>
</body>
</html>
```